Power Point Template Vierklang sustainability consulting

(find english description below)
We are a small German start-up that offers sustainability consulting. For presentations of results, our company presentation, proposals, lectures, etc., we need a PowerPoint template that matches our logo. We come from classic management consulting / strategy consulting and also deal with facts and figures in sustainability consulting. Therefore, the template should not be too fancy and should not only consist of photos. But it shouldn't be a completely sober template either. Our logo with the green leaves for sustainability (three leaves for VIERklang) and the white bar chart (with the dynamic swing upwards) reflects our attitude well, where we see ourselves on the range from playful to sober and classic to modern.

It might be nice for the template to include the shape of one of the leaves (from the logo). Also, the logo should appear in a corner of each slide. The colors from the logo (see appendix) should be partially reflected in the presentation. We can also imagine a gold-brown tone (see website www.vierklang-beratung.de) or a coral tone as a contrast. (Attention - the website is not final yet).

For a first suggestion, it is sufficient to suggest three to four slides (cover sheet, chapter/separation slide, text slide, data slide). We will then mark drafts that we like. In total, we would then need about 6-10 more slide templates, e.g. about us, team, slide for a statement, 2-3 data charts (pie, bar, column), top 3 - 5 list, timeline, contact (more slides are welcome ).

We are a small German start-up offering sustainability consulting. We need a power point template for result presentations, our company presentation, proposals, lectures etc. The template should be aligned with our logo. Our background lies in classic management consulting / strategy consulting and we also deal with facts and figures in sustainability consulting. Therefore, the template should not be too playful and not only consist of photos. But it should also not be a completely clear template. Our logo with the green leaves for sustainability (three leaves for VIERklang) and the white bar chart (with the dynamic upward swing) reflects our attitude well, where we see ourselves on the range from playful to down-to-earth and classic to modern .

For the template, it might be nice to incorporate the shape of one of the leaves (from the logo). Also, the logo should show up in one corner on each slide. Some of the colors from the logo (see attachment) should be reflected in the presentation. We could also think of a gold-brown tone (see website www.vierklang-beratung.de) or a coral tone for contrast. (Attention - the website is not final yet).

For a first proposal it is quite sufficient to suggest us three to four slides (cover page, chapter/separation slide, text slide, data slide). We will then mark the drafts that we like. In total we would need about 6-10 more slide templates, eg About us, Team, slide for a statement, 2-3 data charts (pie, bar, column), Top 3 - 5 List, Timeline, Contact (more slides are welcome).

Target Market(s)

Corporations, large companies and SMEs

Industry/Entity Type

Unternehmensberatung, Nachhaltigkeitsberatung

Font styles to use
Sans Serif
Other font styles liked:
• Calibri

Colors
00AB8E
00BBA5
67D7C9
C6EFE9
E9F9F6

Requirements
Must have
• see description (e.g. the colors of our logo)
Nice to have
• see description (e.g. elements of the logo included)
Should not have
• see description

```html
<!DOCTYPE html>
<html lang="en">
<head>
<meta charset="utf-8">
<title>Vierklang Sustainability Consulting – Slide Template</title>
<link href="https://fonts.googleapis.com/css2?family=Fira+Sans:wght@400;600;700&family=Carlito:wght@400;700&display=swap" rel="stylesheet">
<style>
:root{
  --page:#808080;
  --green-dark:#2f5a10;
  --green-mid:#4f7e1f;
  --green:#8bb23a;
  --green-light:#cddf78;
  --green-pale:#e9f1d8;
  --brown:#8b4a0c;
  --ink:#333;
  --grey-text:#555;
  --slide-grey:#f2f2f2;
}
*{box-sizing:border-box;margin:0;padding:0}
html,body{width:1200px;height:4231px;overflow:hidden}
body{background:var(--page);font-family:"Carlito",Calibri,sans-serif;color:var(--ink);position:relative}
.slide{position:absolute;left:59px;width:1082px;height:607px;overflow:hidden;background:#fff}
.s-cover{top:84px;background:linear-gradient(135deg,#f7f7f7 0%,#ececec 45%,#f6f6f6 60%,#e9e9e9 100%)}
.s-about{top:762px}
.s-pie{top:1448px;background:linear-gradient(160deg,#f4f6ef 0%,#e6ecdc 55%,#eef1e8 100%)}
.s-timeline{top:2139px}
.s-team{top:2842px;background:linear-gradient(170deg,#eef3e2 0%,#e2ebcf 100%)}
.s-contact{top:3538px}

.brand{position:absolute;display:flex;align-items:center;gap:8px;font-family:"Fira Sans",sans-serif;font-weight:400;color:var(--green-mid)}
.brand .dot{border-radius:50%;background:var(--green-mid)}
.brand-small{top:14px;right:62px;font-size:22px}
.brand-small .dot{width:14px;height:14px}

h1,h2{font-family:"Fira Sans",sans-serif;font-weight:700;position:absolute}
h2{font-size:38px;color:var(--green-dark);letter-spacing:.5px}

/* cover */
.cover-mark{position:absolute;left:10px;top:90px;width:470px;height:470px;border-radius:50%;background:radial-gradient(circle at 35% 35%,var(--green-light),var(--green) 70%)}
.cover-brand{top:35px;left:661px;width:366px;height:102px;background:#fff;justify-content:center;font-size:54px;gap:14px}
.cover-brand .dot{width:40px;height:40px}
.cover-title{right:64px;top:262px;text-align:right;font-size:58px;line-height:74px;color:var(--brown);letter-spacing:1px}

/* about */
.circle{position:absolute;border-radius:50%}
.c-dark{left:-51px;top:-51px;width:280px;height:280px;background:var(--green-dark)}
.c-light{left:301px;top:15px;width:124px;height:124px;background:var(--green-light)}
.c-bottom{left:251px;top:520px;width:96px;height:96px;background:var(--green-light);filter:saturate(.9)}
.about-photo{position:absolute;left:59px;top:138px}
.about-title{left:614px;top:118px}
.about-text{position:absolute;left:614px;top:200px;width:392px;font-size:13.5px;line-height:25.4px;color:var(--grey-text);text-align:justify}

/* pie */
.pie-title{left:64px;top:58px}
.donut{position:absolute;left:140px;top:189px;width:338px;height:338px;border-radius:50%;
  background:conic-gradient(var(--green-light) 0deg 25deg,var(--green) 25deg 90deg,var(--green-mid) 90deg 180deg,var(--green-dark) 180deg 325deg,var(--green-light) 325deg 360deg)}
.donut-hole{position:absolute;left:61px;top:61px;width:216px;height:216px;border-radius:50%;background:#fff;display:flex;align-items:center;justify-content:center}
.donut-hole span{width:110px;height:110px;border-radius:50%;background:var(--green-pale)}
.pie-label{position:absolute;color:#fff;font-family:"Fira Sans",sans-serif;font-size:16px;transform:translate(-50%,-50%)}
.cards{position:absolute;left:542px;top:71px;width:500px}
.card{height:107px;margin-bottom:17px;background:linear-gradient(90deg,rgba(236,236,236,.95),rgba(240,240,240,.6));border-left:3px solid var(--brown);padding:24px 28px 0 28px}
.card:first-child{border-left-color:var(--green-mid)}
.card h3{font-family:"Carlito",sans-serif;font-weight:700;font-size:13px;color:#222;margin-bottom:12px}
.card p{font-size:11.5px;line-height:18px;color:#555}

/* timeline */
.tl-title{left:0;width:100%;text-align:center;top:56px}
.tl-line{position:absolute;left:0;right:0;top:314px;height:2px;background:var(--brown)}
.tl-node{position:absolute;top:266px;width:98px;height:98px;margin-left:-49px;border-radius:50%;border:2px solid var(--green-mid);background:#fff;display:flex;align-items:center;justify-content:center}
.tl-node span{width:80px;height:80px;border-radius:50%;display:flex;align-items:center;justify-content:center;color:#fff;font-family:"Fira Sans",sans-serif;font-weight:600;font-size:18px}
.n-dark{background:var(--green-dark)}.n-mid{background:var(--green-mid)}.n-light{background:#6f9c2f}
.tl-stem{position:absolute;width:2px;background:var(--green-mid)}
.tl-stem::after{content:"";position:absolute;left:-3px;width:8px;height:8px;border-radius:50%;background:var(--green-mid)}
.stem-up{top:187px;height:80px}.stem-up::after{top:-4px}
.stem-down{top:364px;height:80px}.stem-down::after{bottom:-4px}
.tl-text{position:absolute;width:150px;font-size:11px;line-height:19.5px;color:#555}
.tl-deco{position:absolute;border-radius:50%;background:#dde8cd;width:300px;height:300px}

/* team */
.team-title{left:0;width:100%;text-align:center;top:54px}
.member{position:absolute;top:169px;width:224px;margin-left:-112px;text-align:center}
.member .photo{width:212px;height:176px;margin:0 auto;background:linear-gradient(180deg,#c9c2b6,#8d8272)}
.member .name{height:38px;background:#fff;margin-top:3px;display:flex;align-items:center;justify-content:center;font-family:"Fira Sans",sans-serif;font-weight:600;font-size:15px;color:var(--green-mid)}
.member .bio{margin-top:24px;font-size:11px;line-height:19px;color:#444}
.social{display:flex;justify-content:center;gap:9px;margin-top:13px}
.social span{width:34px;height:34px;border-radius:50%;border:1.5px solid var(--brown)}

/* contact */
.contact-photo{position:absolute;left:0;top:0}
.contact-brand{left:671px;top:74px;font-size:56px;gap:14px}
.contact-brand .dot{width:44px;height:44px}
.thanks{position:absolute;left:660px;width:326px;top:212px;display:flex;align-items:center;gap:16px;font-family:"Fira Sans",sans-serif;font-weight:700;font-size:36px;color:var(--green-mid);white-space:nowrap}
.thanks::before,.thanks::after{content:"";flex:1;height:2px;background:var(--green)}
.presenter{position:absolute;left:732px;top:315px;font-family:"Fira Sans",sans-serif;font-size:17px;color:#444}
.contact-list{position:absolute;left:730px;top:362px;list-style:none}
.contact-list li{display:flex;align-items:flex-start;gap:12px;font-size:11.5px;line-height:16px;color:#555;margin-bottom:20px}
.contact-list svg{flex:none;width:18px;height:18px;fill:var(--green-mid)}
</style>
</head>
<body>

<section class="slide s-cover">
  <div class="cover-mark"></div>
  <div class="brand cover-brand"><span class="dot"></span>Vierklang</div>
  <h1 class="cover-title">VIERKLANG<br>SUSTAINABILITY<br>CONSULTING</h1>
</section>

<section class="slide s-about">
  <div class="circle c-dark"></div>
  <div class="circle c-light"></div>
  <svg class="about-photo" width="482" height="400" viewBox="0 0 482 400" role="img" aria-label="Photo of consultants in a meeting around a table, set in a leaf shape">
    <defs><linearGradient id="aboutGrad" x1="0" y1="1" x2="1" y2="0"><stop offset="0" stop-color="#3b3633"/><stop offset=".55" stop-color="#8c7b6e"/><stop offset="1" stop-color="#d9d3cc"/></linearGradient></defs>
    <path d="M0 400 C30 170 240 20 482 0 C475 190 320 385 0 400 Z" fill="url(#aboutGrad)"/>
  </svg>
  <div class="circle c-bottom"></div>
  <div class="brand brand-small"><span class="dot"></span>Vierklang</div>
  <h2 class="about-title">ABOUT US</h2>
  <p class="about-text">The ever- increasing demands in terms of social, ecological and economic concerns have been presenting companies with growing challenges for years. Not only do the increasing legal requirements speak in favor of actively shaping one's own future , but also the increasing demand from consumers for sustainable products and the increasing interest of employees in sustainable aspects of corporate culture . The complexity of sustainability offers long-term solutions for sustainable business.</p>
</section>

<section class="slide s-pie">
  <div class="brand brand-small"><span class="dot"></span>Vierklang</div>
  <h2 class="pie-title">PIE CHART</h2>
  <div class="donut">
    <div class="donut-hole"><span></span></div>
    <span class="pie-label" style="left:174px;top:29px">5</span>
    <span class="pie-label" style="left:287px;top:95px">15</span>
    <span class="pie-label" style="left:267px;top:271px">30</span>
    <span class="pie-label" style="left:28px;top:171px">45</span>
  </div>
  <div class="cards">
    <div class="card"><h3>Lorem ipsum dolor sit amet, consectetur adipiscing</h3><p>Lorem ipsum dolor sit amet, consectetur adipiscing elit, sed do eiusmod tempor incididunt ut labore et dolore magna aliqua.</p></div>
    <div class="card"><h3>Lorem ipsum dolor sit amet, consectetur adipiscing</h3><p>Lorem ipsum dolor sit amet, consectetur adipiscing elit, sed do eiusmod tempor incididunt ut labore et dolore magna aliqua.</p></div>
    <div class="card"><h3>Lorem ipsum dolor sit amet, consectetur adipiscing</h3><p>Lorem ipsum dolor sit amet, consectetur adipiscing elit, sed do eiusmod tempor incididunt ut labore et dolore magna aliqua.</p></div>
    <div class="card"><h3>Lorem ipsum dolor sit amet, consectetur adipiscing</h3><p>Lorem ipsum dolor sit amet, consectetur adipiscing elit, sed do eiusmod tempor incididunt ut labore et dolore magna aliqua.</p></div>
  </div>
</section>

<section class="slide s-timeline">
  <div class="tl-deco" style="left:-90px;top:420px"></div>
  <div class="tl-deco" style="left:880px;top:420px"></div>
  <div class="brand brand-small"><span class="dot"></span>Vierklang</div>
  <h2 class="tl-title">OUR TIMELINE</h2>
  <div class="tl-line"></div>

  <div class="tl-stem stem-up" style="left:165px"></div>
  <p class="tl-text" style="left:182px;top:193px">Lorem ipsum dolor sit amet, consectetur adipiscing elit, sed do eiusmod</p>
  <div class="tl-stem stem-down" style="left:337px"></div>
  <p class="tl-text" style="left:354px;top:378px">Lorem ipsum dolor sit amet, consectetur adipiscing elit, sed do eiusmod</p>
  <div class="tl-stem stem-up" style="left:508px"></div>
  <p class="tl-text" style="left:527px;top:193px">Lorem ipsum dolor sit amet, consectetur adipiscing elit, sed do eiusmod</p>
  <div class="tl-stem stem-down" style="left:682px"></div>
  <p class="tl-text" style="left:700px;top:372px">Lorem ipsum dolor sit amet, consectetur adipiscing elit, sed do eiusmod</p>
  <div class="tl-stem stem-up" style="left:853px"></div>
  <p class="tl-text" style="left:871px;top:193px">Lorem ipsum dolor sit amet, consectetur adipiscing elit, sed do eiusmod</p>

  <div class="tl-node" style="left:166px"><span class="n-dark">01</span></div>
  <div class="tl-node" style="left:338px"><span class="n-mid">02</span></div>
  <div class="tl-node" style="left:509px"><span class="n-dark">03</span></div>
  <div class="tl-node" style="left:683px"><span class="n-light">04</span></div>
  <div class="tl-node" style="left:854px"><span class="n-dark">05</span></div>
</section>

<section class="slide s-team">
  <div class="brand brand-small"><span class="dot"></span>Vierklang</div>
  <h2 class="team-title">OUR TEAM</h2>
  <div class="member" style="left:245px">
    <div class="photo" role="img" aria-label="Portrait photo of Marlene Ostrow"></div>
    <div class="name">dr Marlene Ostrow</div>
    <p class="bio">Marlene is co-founder and managing<br>director of Vierklang Consulting GmbH.<br>She has a high level of analytical</p>
    <div class="social"><span></span><span></span><span></span><span></span></div>
  </div>
  <div class="member" style="left:542px">
    <div class="photo" role="img" aria-label="Portrait photo of Jana Feld"></div>
    <div class="name">dr Jana Feld</div>
    <p class="bio">Jana is co-founder and managing<br>director of Vierklang Consulting GmbH.<br>She is very good at systematically</p>
    <div class="social"><span></span><span></span><span></span><span></span></div>
  </div>
  <div class="member" style="left:837px">
    <div class="photo" role="img" aria-label="Portrait photo of Carla Wendt-Ibsen"></div>
    <div class="name">dr Carla Wendt-Ibsen</div>
    <p class="bio">Carla is co-founder and managing<br>director of Vierklang Consulting GmbH.<br>She always manages to react</p>
    <div class="social"><span></span><span></span><span></span><span></span></div>
  </div>
</section>

<section class="slide s-contact">
  <svg class="contact-photo" width="1082" height="607" viewBox="0 0 1082 607" role="img" aria-label="Photo of a business meeting table with a small potted tree, documents and a calculator">
    <defs><linearGradient id="contactGrad" x1="0" y1="0" x2="1" y2="1"><stop offset="0" stop-color="#5d5a52"/><stop offset=".45" stop-color="#a89a82"/><stop offset=".75" stop-color="#c9a66a"/><stop offset="1" stop-color="#6e5a3e"/></linearGradient></defs>
    <path d="M0 0 H640 C560 70 450 170 490 300 C530 430 480 540 505 607 H0 Z" fill="url(#contactGrad)"/>
  </svg>
  <div class="brand contact-brand"><span class="dot"></span>Vierklang</div>
  <div class="thanks">THANK YOU</div>
  <p class="presenter">PRESENTER NAME</p>
  <ul class="contact-list">
    <li><svg viewBox="0 0 24 24"><path d="M6.6 10.8a15.1 15.1 0 0 0 6.6 6.6l2.2-2.2a1 1 0 0 1 1-.25 11.4 11.4 0 0 0 3.6.6 1 1 0 0 1 1 1V20a1 1 0 0 1-1 1A17 17 0 0 1 3 4a1 1 0 0 1 1-1h3.5a1 1 0 0 1 1 1c0 1.25.2 2.45.6 3.6a1 1 0 0 1-.25 1z"/></svg>+49 (0) 6000 – 555 0142</li>
    <li><svg viewBox="0 0 24 24"><path d="M12 2a10 10 0 1 0 0 20 10 10 0 0 0 0-20zm0 2a8 8 0 0 1 7.75 6H15a13 13 0 0 0-2-5.9A8 8 0 0 1 12 4zM4.25 14H9a13 13 0 0 0 2 5.9A8 8 0 0 1 4.25 14zM4.25 10A8 8 0 0 1 11 4.1 13 13 0 0 0 9 10zm6.75 0a11 11 0 0 1 1-4.5 11 11 0 0 1 1 4.5zm0 4h2a11 11 0 0 1-1 4.5 11 11 0 0 1-1-4.5zm2 5.9A13 13 0 0 0 15 14h4.75A8 8 0 0 1 13 19.9z"/></svg>www.vierklangberatung.com</li>
    <li><svg viewBox="0 0 24 24"><path d="M2 5h20v14H2zm2 2v.5l8 5 8-5V7zm0 3v7h16v-7l-8 5z"/></svg>info@vierklang-beratung.de</li>
    <li><svg viewBox="0 0 24 24"><path d="M12 2a7 7 0 0 0-7 7c0 5 7 13 7 13s7-8 7-13a7 7 0 0 0-7-7zm0 9.5A2.5 2.5 0 1 1 12 6.5a2.5 2.5 0 0 1 0 5z"/></svg><span>Sustainability Office Park Lindental<br>Ahornweg 12 60000 Lindental/ Frankfurt a. M</span></li>
  </ul>
</section>

</body>
</html>
```